KLV Plant Services

We are a heavy diesel mechanical business with additional air con certificates, remapping engine rebuilt

Contact Information for Business Card

Company Name, Director Name, Managing Director, Contact details, email and website

Font styles to use
Serif
Script

```html
<!DOCTYPE html>
<html lang="en">
<head>
<meta charset="utf-8">
<title>KLV Plant Services – Business Card</title>
<link href="https://fonts.googleapis.com/css2?family=Arimo:wght@400;700&display=swap" rel="stylesheet">
<style>
  :root {
    --backdrop: #7d7d7d;
    --navy: #03035a;
    --navy-soft: #2a2c9a;
    --paper: #f3f3f5;
    --ink: #0b0b12;
    --white: #ffffff;
  }
  * { box-sizing: border-box; margin: 0; padding: 0; }
  html, body {
    width: 1200px; height: 900px; overflow: hidden;
    background: var(--backdrop);
    font-family: "Arimo", Arial, sans-serif;
  }
  .stage { position: relative; width: 1200px; height: 900px; }
  .card {
    position: absolute; left: 290px;
    width: 620px; height: 354px;
    border-radius: 24px; overflow: hidden;
    box-shadow: 0 10px 24px rgba(0,0,0,0.35);
  }
  .card--back { top: 56px; background: var(--navy); }
  .card--front { top: 490px; background: var(--navy); }

  .back-mark {
    position: absolute; left: 0; right: 0; top: 50%;
    transform: translateY(-50%);
    display: flex; align-items: center; justify-content: center; gap: 14px;
    color: var(--navy-soft); font-weight: 700; font-size: 34px;
  }
  .mark-dot {
    width: 22px; height: 22px; border-radius: 50%;
    background: var(--navy-soft);
  }

  .card-art { position: absolute; inset: 0; }

  .brand {
    position: absolute; left: 52px; top: 156px;
    display: flex; align-items: center; gap: 10px;
    color: var(--navy); font-weight: 700; font-size: 25px;
  }
  .brand .mark-dot { width: 18px; height: 18px; background: var(--navy); }

  .contact {
    position: absolute; right: 34px; top: 60px;
    text-align: right; color: var(--white);
  }
  .contact__name { font-size: 24px; font-weight: 700; }
  .contact__title { font-size: 15px; margin-top: 2px; }
  .contact__address { font-size: 15px; line-height: 20px; margin-top: 48px; }
  .contact__lines { list-style: none; margin-top: 18px; font-size: 15px; line-height: 21px; }
  .contact__lines li { display: flex; justify-content: flex-end; align-items: center; gap: 8px; }
  .contact__lines svg { width: 13px; height: 13px; fill: var(--white); }
</style>
</head>
<body>
<main class="stage">
  <section class="card card--back" aria-label="Card back">
    <div class="back-mark"><span class="mark-dot"></span>KLV Plant Services</div>
  </section>

  <section class="card card--front" aria-label="Card front">
    <svg class="card-art" viewBox="0 0 620 354" aria-hidden="true">
      <path d="M0 0 H268 C380 40 410 250 338 354 H0 Z" fill="var(--paper)"/>
      <path d="M150 28 C250 -10 360 40 372 170 C382 270 320 340 210 330
               C300 322 360 262 356 168 C348 70 270 20 150 28 Z" fill="var(--ink)"/>
    </svg>

    <div class="brand"><span class="mark-dot"></span>KLV Plant Services</div>

    <div class="contact">
      <p class="contact__name">Daniel Harper</p>
      <p class="contact__title">Managing Director</p>
      <p class="contact__address">2719 Ashford Lane<br>Millbrook, NY 12545</p>
      <ul class="contact__lines">
        <li>(555) 2914-6038
          <svg viewBox="0 0 16 16"><path d="M3 1h3l1.5 4-2 1.3a9 9 0 0 0 4.2 4.2L11 8.5l4 1.5v3a2 2 0 0 1-2 2A12 12 0 0 1 1 3a2 2 0 0 1 2-2z"/></svg></li>
        <li>name@KLVplant.com
          <svg viewBox="0 0 16 16"><path d="M1 3h14v10H1z M2 4l6 5 6-5" fill="none" stroke="#fff" stroke-width="1.6"/></svg></li>
        <li>www.KLVplant.com
          <svg viewBox="0 0 16 16"><circle cx="8" cy="8" r="6.5" fill="none" stroke="#fff" stroke-width="1.6"/><path d="M1.5 8h13M8 1.5c-3 3.5-3 9.5 0 13M8 1.5c3 3.5 3 9.5 0 13" fill="none" stroke="#fff" stroke-width="1.2"/></svg></li>
      </ul>
    </div>
  </section>
</main>
</body>
</html>
```